Veranix - Solution provider in business consulting

Veranix is a swiss based company providing solutions for developing markets. The business covers various fields of business consulting, such as supply chain, product costs, quality management and manufacturing management. The Business operates in a efficient, straight and solution oriented manner.
The final design should communicate these characteristics. Asian people as well as as western people shall identify the qualities of the company at first sight.
The customer needs business cards with a simple view but an recognizable design, printed in high quality. Engraved elements such as the globe or simple words are possible.
Available colors are: (RAL)
102/102/102
51/102/102
153/204/153
255/102/51
Font: Calibri

```html
<!DOCTYPE html>
<html lang="en">
<head>
<meta charset="utf-8">
<title>Veranix business cards</title>
<link rel="stylesheet" href="https://fonts.googleapis.com/css2?family=Carlito:wght@400;700&display=swap">
<style>
  :root {
    --ink: #666666;
    --band: #666666;
    --paper: #ffffff;
    --backdrop: #e9e7e4;
    --reverse-text: #ffffff;
  }
  * { margin: 0; padding: 0; box-sizing: border-box; }
  html, body {
    width: 1200px; height: 900px; overflow: hidden;
    background: var(--backdrop);
    font-family: "Carlito", Calibri, sans-serif;
    color: var(--ink);
  }
  .stage { position: relative; width: 1200px; height: 900px; }

  .card { position: absolute; background: var(--paper); overflow: hidden;
          box-shadow: 0 4px 14px rgba(0,0,0,0.18); }

  /* front */
  .card-front { left: 77px; top: 35px; width: 588px; height: 363px; }
  .front-wordmark { position: absolute; left: 36px; top: 40px; font-size: 48px;
                    font-weight: 400; line-height: 1; letter-spacing: 0.5px; }
  .holder { position: absolute; left: 350px; top: 101px; }
  .holder-name { font-size: 21px; font-weight: 700; line-height: 26px; }
  .holder-role { font-size: 16px; line-height: 20px; }
  .address { position: absolute; left: 350px; top: 168px; font-size: 16px; line-height: 24px; }
  .contacts { position: absolute; left: 350px; top: 231px; list-style: none;
              font-size: 16px; line-height: 24.5px; }
  .contacts li { display: flex; align-items: center; gap: 10px; }
  .contacts svg { width: 12px; height: 12px; fill: var(--ink); flex: none; }
  .front-band { position: absolute; left: 0; bottom: 0; width: 100%; height: 25px;
                background: var(--band); }

  /* back */
  .card-back { left: 388px; top: 506px; width: 566px; height: 351px; }
  .back-panel { position: absolute; left: 0; top: 0; width: 100%; height: 264px;
                background: var(--band); }
  .back-web { position: absolute; left: 0; top: 114px; width: 100%; text-align: center;
              color: var(--reverse-text); font-size: 17px; font-weight: 700; }
  .back-web strong { font-size: 27px; }
  .back-wordmark { position: absolute; right: 30px; bottom: 20px; font-size: 56px;
                   font-weight: 400; line-height: 1; letter-spacing: 0.5px; }
</style>
</head>
<body>
<main class="stage">
  <section class="card card-front" aria-label="Business card front">
    <div class="front-wordmark">veranix</div>
    <div class="holder">
      <p class="holder-name">Marco Lindt</p>
      <p class="holder-role">CEO</p>
    </div>
    <address class="address" style="font-style:normal">
      Veranix GmbH Feldweg 14<br>8570 Weinfelden Switzerland
    </address>
    <ul class="contacts">
      <li><svg viewBox="0 0 12 12" aria-hidden="true"><path d="M3 0h6a1 1 0 0 1 1 1v10a1 1 0 0 1-1 1H3a1 1 0 0 1-1-1V1a1 1 0 0 1 1-1zm0.5 1.5v8h5v-8z"/></svg>+41 79 382 5067</li>
      <li><svg viewBox="0 0 12 12" aria-hidden="true"><path d="M2.5 0.5l2 2.5-1.2 1.3c.7 1.6 2 2.9 3.4 3.6L8 6.6l2.7 2-1.2 2.6C5 11 1 7 0.8 2z"/></svg>+41 71 624 3188</li>
      <li><svg viewBox="0 0 12 12" aria-hidden="true"><path d="M0 2h12v8H0zm1 1l5 3.5L11 3z" /></svg>marco.lindt@veranix.ch</li>
      <li><svg viewBox="0 0 12 12" aria-hidden="true"><circle cx="6" cy="6" r="6"/></svg>www.veranix.ch</li>
    </ul>
    <div class="front-band"></div>
  </section>

  <section class="card card-back" aria-label="Business card back">
    <div class="back-panel"></div>
    <p class="back-web">www.<strong>veranix</strong>.ch</p>
    <div class="back-wordmark">veranix</div>
  </section>
</main>
</body>
</html>
```